Quorbelline.io - Please redesign to make it look better from current design

We already have the current website, that you can access but we think it can improve from current version.
Quorbelline is a cryptocurrency hedge fund that allow you to participate in the hedge fund with cryptocurrency such as eth.
At current phase, we are doing an ICO, then we want to make sure that the website it looks professional, beautiful and trustable enough for investors after looking at our website.
Target Market(s)
Investors
Industry/Entity Type
Investment
Coding
Coded - Design and coding required
Number of Pages Required
1 page
Look and feel
Each slider illustrates characteristics of the customer's brand and the style your logo design should communicate.

```html
<!DOCTYPE html>
<html lang="en">
<head>
<meta charset="utf-8">
<title>Quorbelline.io — Digital Asset Management</title>
<link href="https://fonts.googleapis.com/css2?family=Roboto:wght@300;400;500;700&family=Open+Sans:ital,wght@0,400;0,600;1,400&display=swap" rel="stylesheet">
<style>
:root{
  --navy:#14248a;
  --navy-dark:#0f1c74;
  --ice:#c8ebff;
  --grey-bg:#eeeeee;
  --ink:#333;
  --muted:#666;
  --line:#d6d6d6;
  --white:#fff;
}
*{margin:0;padding:0;box-sizing:border-box}
html,body{width:1200px;height:2980px;overflow:hidden}
body{font-family:"Open Sans",sans-serif;color:var(--ink);background:var(--white);position:relative}
.abs{position:absolute}

/* header */
.brand{left:80px;top:22px;display:flex;align-items:center;gap:12px}
.brand-dot{width:40px;height:40px;border-radius:50%;background:var(--navy)}
.brand-name{font-family:"Roboto",sans-serif;font-weight:500;font-size:22px;color:var(--navy)}
.nav{top:52px;left:0;width:1200px;font-family:"Roboto",sans-serif;font-size:16px;color:#111}
.nav a{position:absolute;color:inherit;text-decoration:none}

/* hero */
.hero-title{left:78px;top:240px;font-family:"Roboto",sans-serif;font-weight:300;font-size:82px;color:var(--navy);letter-spacing:1px}
.hero-sub{left:80px;top:356px;font-family:"Roboto",sans-serif;font-weight:300;font-size:38px;color:var(--navy)}
.hero-rule{left:80px;top:434px;width:62px;height:3px;background:var(--navy)}
.hero-copy{left:80px;top:464px;width:540px;font-size:18px;line-height:27px;color:#555}
.hero-art{left:600px;top:120px;width:600px;height:560px;background:radial-gradient(circle at 55% 50%,#e4e9fb 0%,#f6f8ff 55%,#fff 80%)}

/* about */
.band{left:0;width:1200px;background:var(--navy)}
.about{top:680px;height:464px}
.about-screen{left:78px;top:60px;width:482px;height:392px;background:linear-gradient(180deg,#1c1c1c 0%,#2a2a2a 68%,#cfd2d6 70%,#e6e8eb 100%);border-radius:6px}
.section-title{font-family:"Roboto",sans-serif;font-weight:300;font-size:40px;color:var(--white);letter-spacing:.5px}
.about-title{left:628px;top:50px}
.about-copy{left:628px;top:112px;width:478px;font-size:15px;line-height:25px;color:var(--white)}
.btn{display:flex;align-items:center;justify-content:center;background:var(--ice);color:var(--navy);font-family:"Roboto",sans-serif;font-weight:700;font-size:15px;letter-spacing:.3px}
.about-btn{left:626px;top:358px;width:166px;height:52px}

/* team */
.team{top:1144px;left:0;width:1200px;height:566px;background:var(--grey-bg)}
.team-title{left:0;width:1200px;top:44px;text-align:center;font-family:"Roboto",sans-serif;font-weight:300;font-size:40px;color:#111}
.card{top:126px;width:322px;height:386px;background:var(--white);box-shadow:0 3px 8px rgba(0,0,0,.12)}
.card-photo{left:8px;top:16px;width:90px;height:90px;border-radius:50%;background:linear-gradient(160deg,#8a6d5a,#3a2e2a)}
.card-role{left:110px;top:34px;font-style:italic;font-size:14px;color:#333}
.card-name{left:110px;top:58px;font-family:"Roboto",sans-serif;font-size:17px;color:var(--navy)}
.card-rule{left:0;top:120px;width:322px;height:1px;background:var(--line)}
.card-copy{left:12px;top:138px;width:300px;font-size:14.5px;line-height:25px;color:#666}

/* process */
.process{top:1710px;height:420px}
.process-title{left:80px;top:46px}
.process-sub{left:80px;top:130px;font-family:"Roboto",sans-serif;font-size:28px;color:var(--white)}
.process-copy{left:80px;top:180px;width:540px;font-size:15.5px;line-height:26px;color:var(--white)}
.process-art{left:650px;top:56px;width:440px;height:350px;background:linear-gradient(160deg,#e9ecf7 0%,#9aa3bd 60%,#3d4154 100%);border-radius:4px}

/* profit */
.profit{top:2130px;left:0;width:1200px;height:514px}
.profit-title{left:0;width:1200px;top:46px;text-align:center;font-family:"Roboto",sans-serif;font-size:28px;color:var(--navy)}
.tier{font-family:"Roboto",sans-serif;font-size:19px;color:#333;white-space:nowrap}
.tier small{font-size:14px}
.tier-note{display:block;font-family:"Open Sans",sans-serif;font-size:13.5px;color:#444}
.profit-foot{left:0;width:1200px;top:424px;text-align:center;font-size:16px;color:#333}

/* footer */
.footer{top:2644px;height:336px}
.f-head{font-family:"Roboto",sans-serif;font-weight:500;font-size:19px;color:var(--white);letter-spacing:.3px}
.f-copy{font-size:15px;line-height:25px;color:var(--white)}
.f-btn{left:80px;top:176px;width:166px;height:52px}
.f-brand{left:356px;top:92px;display:flex;align-items:center;gap:10px;font-family:"Roboto",sans-serif;font-size:19px;color:var(--white);letter-spacing:2px}
.pin{width:18px;height:22px}
.f-field{left:644px;top:170px;width:220px;height:52px;background:var(--white);font-size:14px;color:#888;padding:16px 22px}
.f-send{left:864px;top:170px;width:52px;height:52px;background:var(--ice);display:flex;align-items:center;justify-content:center}
.f-logo{left:958px;top:56px;width:150px;height:150px;border-radius:50%;background:var(--white);display:flex;align-items:center;justify-content:center;font-family:"Roboto",sans-serif;font-weight:500;font-size:20px;color:var(--navy)}
.f-socials{left:958px;top:234px;display:flex;gap:14px}
.f-socials span{width:40px;height:40px;border-radius:50%;background:var(--ice)}
.f-rule{left:80px;top:294px;width:1040px;height:1px;background:rgba(255,255,255,.25)}
.f-legal{left:0;width:1200px;top:306px;text-align:center;font-size:15px;color:var(--white)}
.f-legal b{font-weight:600}
</style>
</head>
<body>

<header>
  <div class="abs brand"><span class="brand-dot"></span><span class="brand-name">quorbelline</span></div>
  <nav class="abs nav">
    <a style="left:642px">Home</a>
    <a style="left:738px">About</a>
    <a style="left:830px">Process</a>
    <a style="left:940px">Our Team</a>
    <a style="left:1062px">Contact</a>
  </nav>
</header>

<section class="hero">
  <h1 class="abs hero-title">quorbelline</h1>
  <p class="abs hero-sub">Digital Asset Management</p>
  <div class="abs hero-rule"></div>
  <p class="abs hero-copy">Quorbelline enable companies and investors to facilities business operation in modern digital world, including asset management on hedge fund strategy model.</p>
  <div class="abs hero-art" role="img" aria-label="Line illustration of crypto coins, a rocket, charts, wallet and payment icons connected by lines"></div>
</section>

<section class="abs band about">
  <div class="abs about-screen" role="img" aria-label="Desktop monitor showing a bar chart of a $100,000 investment growth"></div>
  <h2 class="abs section-title about-title">ABOUT US</h2>
  <p class="abs about-copy">Quorbelline process and manages on hedge fund strategy models which invests in a diversified portfolio of blockchain tokens. Blockchain tokens are emerging which add a monetary incentive layer to p2p protocols and facilitate equity crowdfunding that anyone in the world can participate in. This means open source software developers can monetize their networks at the protocol level and users of the network are the equity owners of the network. For this conditions, returns will go to holders of the tokens.</p>
  <a class="abs btn about-btn">EXPLORE MORE</a>
</section>

<section class="abs team">
  <h2 class="abs team-title">EXECUTIVE TEAM</h2>

  <article class="abs card" style="left:80px">
    <div class="abs card-photo" role="img" aria-label="Portrait photo of the director"></div>
    <p class="abs card-role">Director</p>
    <p class="abs card-name">Dariel Vontashek</p>
    <div class="abs card-rule"></div>
    <p class="abs card-copy">As a hedge fund manager. Vontashek is the Chief Executive Officer of Bramblewick Capital LLC, an investment manager of Ostley Ridge Fund SP (Long-Short Equity Fund, investing in U.S. Stock Market) and Kestrel Arc Fund (Managed Futures Fund, focusing in Japanese Futures Market) Both based in Tokyo.</p>
  </article>

  <article class="abs card" style="left:442px">
    <div class="abs card-photo" role="img" aria-label="Portrait photo of the technical advisor" style="background:linear-gradient(160deg,#c9d3c4,#5f6b5a)"></div>
    <p class="abs card-role">Technical advisor</p>
    <p class="abs card-name">Ilmaro Pekkintu</p>
    <div class="abs card-rule"></div>
    <p class="abs card-copy">Pekkintu has various experienced on cryptocurrency and blockchain technology. He created what was the world's 4th most valuable cryptocurrency in February 2014. He is also the world's first person to implement stealth addresses in Veltra Wallets, improving cryptocurrency anonymity.</p>
  </article>

  <article class="abs card" style="left:806px">
    <div class="abs card-photo" role="img" aria-label="Portrait photo of the marketing consultant" style="background:linear-gradient(160deg,#a0523e,#3b2420)"></div>
    <p class="abs card-role">Marketing Consultant</p>
    <p class="abs card-name">Sorvan Keltrimowa</p>
    <div class="abs card-rule"></div>
    <p class="abs card-copy">Keltrimowa embeds a decade of experience in brand building, strategic planning, and marketing communication across the global agencies, such as Harrow Northline, Pellmark, Ardent Vale, Sunmori. His seasoned specialty focuses on exploring a new market insight to formulate disruptive strategies</p>
  </article>
</section>

<section class="abs band process">
  <h2 class="abs section-title process-title">PROCESS</h2>
  <h3 class="abs process-sub">Hedge Fund Model</h3>
  <p class="abs process-copy">Quorbelline run on closed-end fund (CEF) model which offers its shares to investors and utilize the fund to speculate and invest in the innovative blockchain tokens. Quorbelline will charge an upfront annual operation fee 4% of the money raised during the ICO. After that, the fund will charge a quarterly performance of 50% on the net profit made.</p>
  <div class="abs process-art" role="img" aria-label="Cartoon businessman pointing at a laptop screen listing market volumes"></div>
</section>

<section class="abs profit">
  <h2 class="abs profit-title">Net Profit Distribution</h2>
  <svg class="abs" style="left:0;top:0" width="1200" height="514" viewBox="0 0 1200 514" aria-hidden="true">
    <g stroke="#cfcfcf" stroke-width="1.5" fill="none">
      <line x1="604" y1="198" x2="604" y2="158"/>
      <polyline points="518,262 460,228 220,228"/>
      <polyline points="690,262 750,228 1010,228"/>
      <polyline points="548,368 500,394 230,394"/>
      <polyline points="660,368 710,394 980,394"/>
    </g>
    <polygon points="604,198 690,262 660,368 548,368 518,262" fill="#cfeeff"/>
    <g fill="#14248a">
      <circle cx="604" cy="198" r="4"/>
      <circle cx="690" cy="262" r="4"/>
      <circle cx="660" cy="368" r="4"/>
      <circle cx="548" cy="368" r="4"/>
      <circle cx="518" cy="262" r="4"/>
    </g>
    <text x="604" y="294" text-anchor="middle" font-family="Roboto, sans-serif" font-weight="500" font-size="17" fill="#14248a">quorbelline</text>
  </svg>
  <div class="abs tier" style="left:0;width:1200px;top:100px;text-align:center">50 %<span class="tier-note">of net profit is distributed to investors</span></div>
  <div class="abs tier" style="left:214px;top:164px">0 – 5 % <small>net profit</small> &gt; 0%<span class="tier-note">performance fee</span></div>
  <div class="abs tier" style="left:784px;top:164px">&gt; 15% <small>net profit</small> &gt; 15%<span class="tier-note">performance fee</span></div>
  <div class="abs tier" style="left:252px;top:330px">5 – 10% <small>net profit</small> &gt; 5%<span class="tier-note">performance fee</span></div>
  <div class="abs tier" style="left:746px;top:330px">10-15 % <small>net profit</small> &gt; 13%<span class="tier-note">performance fee</span></div>
  <p class="abs profit-foot">The remainder (50% minus performance fee, so at least 35%) is reinvested</p>
</section>

<footer class="abs band footer">
  <h4 class="abs f-head" style="left:80px;top:40px">FOR MORE INFO</h4>
  <p class="abs f-copy" style="left:80px;top:78px;width:240px">Lorem Ipsum is simply dummy text of the printing and typesetting industry. Lorem Ipsum has been the industry's.</p>
  <a class="abs btn f-btn">DOWNLOAD PDF</a>

  <h4 class="abs f-head" style="left:356px;top:40px">CONTACT INFO</h4>
  <div class="abs f-brand">
    <svg class="pin" viewBox="0 0 18 22" aria-hidden="true"><path d="M9 0C4 0 0 4 0 8.6 0 14.5 9 22 9 22s9-7.5 9-13.4C18 4 14 0 9 0zm0 12.2a3.6 3.6 0 1 1 0-7.2 3.6 3.6 0 0 1 0 7.2z" fill="#fff"/></svg>
    <span>quorbelline</span>
  </div>
  <p class="abs f-copy" style="left:386px;top:128px;width:220px">Suites 08-12, 21/F, Lindqvist Tower, Marrow Quay Centre, 44 Marrow Quay Road, Eastgate, Port Halden.</p>

  <h4 class="abs f-head" style="left:644px;top:40px">NEWSLETTER</h4>
  <p class="abs f-copy" style="left:644px;top:78px;width:260px">Subscribe to Our Newsletter to get latest News &amp; Updates About Company</p>
  <div class="abs f-field">Enter Your E-Mail</div>
  <div class="abs f-send">
    <svg width="22" height="22" viewBox="0 0 24 24" aria-hidden="true"><path d="M2 11 22 2l-7 20-3-8-10-3zm10 3 10-12" fill="none" stroke="#14248a" stroke-width="1.8" stroke-linejoin="round"/></svg>
  </div>

  <div class="abs f-logo">quorbelline</div>
  <div class="abs f-socials"><span></span><span></span><span></span></div>

  <div class="abs f-rule"></div>
  <p class="abs f-legal">© <b>quorbelline</b> - 2017. All Rights Reserved.</p>
</footer>

</body>
</html>
```